Need flyer for honey

I need the advertising flyer for my honey products. Will need around 4-6 page A5 size. Flyer content is ready but will need to check the wording and need the artwork and pictures designed in a proper manner.

Advertising

```html
<!DOCTYPE html>
<html lang="en">
<head>
<meta charset="utf-8">
<title>Amber Meadow – Pure Australia Honey Flyer</title>
<link rel="stylesheet" href="https://fonts.googleapis.com/css2?family=Arimo:wght@400;700&family=Cinzel:wght@400&family=Lato:wght@300;400&display=swap">
<style>
  :root {
    --paper: #ffffff;
    --honey-yellow: #f7e41d;
    --title-yellow: #f2e23a;
    --ink: #2b2b2b;
    --ink-soft: #3a3a3a;
    --amber-deep: #e0a62a;
    --amber-light: #f6d889;
    --leaf: #6f9a3a;
  }
  * { box-sizing: border-box; margin: 0; padding: 0; }
  html, body {
    width: 1200px; height: 849px; overflow: hidden;
    background: var(--paper);
  }
  .flyer {
    position: relative; width: 1200px; height: 849px;
    background: var(--paper);
    font-family: "Arimo", Arial, sans-serif;
    color: var(--ink);
  }

  /* Left panel */
  .mission-box {
    position: absolute; left: 37px; top: 40px; width: 525px; height: 284px;
    background: var(--honey-yellow);
    padding: 18px 34px 0 32px;
    font-size: 13.2px; line-height: 1.18; color: var(--ink-soft);
    text-align: justify;
  }
  .mission-box p + p { margin-top: 7px; }
  .brand-mark {
    position: absolute; left: 150px; top: 395px;
    display: flex; align-items: center; gap: 14px;
  }
  .brand-mark .dot {
    width: 44px; height: 44px; border-radius: 50%;
    background: var(--honey-yellow);
  }
  .brand-mark .name {
    font-family: "Arimo", Arial, sans-serif; font-weight: 700;
    font-size: 40px; color: var(--ink); letter-spacing: -0.5px;
  }
  .photo-blossom {
    position: absolute; left: 26px; top: 500px; width: 567px; height: 195px;
    background:
      radial-gradient(ellipse 18% 28% at 20% 62%, #e9b04a 0%, #d9a25a 60%, transparent 100%),
      radial-gradient(ellipse 42% 40% at 52% 30%, #f3e3dc 0%, #efd6cf 55%, transparent 100%),
      radial-gradient(ellipse 30% 20% at 55% 72%, #8fb25a 0%, transparent 100%),
      linear-gradient(180deg, #ffffff 0%, #fbf7f2 100%);
  }
  .address {
    position: absolute; left: 58px; top: 752px; width: 482px;
    font-family: "Lato", Arial, sans-serif; font-size: 13.5px; line-height: 1.25;
    text-align: center; color: var(--ink);
  }

  /* Right panel */
  .brand-small {
    position: absolute; left: 1030px; top: 52px;
    display: flex; align-items: center; gap: 6px;
  }
  .brand-small .dot {
    width: 18px; height: 18px; border-radius: 50%;
    background: var(--honey-yellow);
  }
  .brand-small .name {
    font-weight: 700; font-size: 17px; color: var(--ink);
  }
  .title-pure {
    position: absolute; left: 700px; top: 140px; width: 400px; text-align: center;
    font-family: "Lato", Arial, sans-serif; font-weight: 400; font-size: 22px;
    letter-spacing: 1px; color: var(--title-yellow);
  }
  .title-main {
    position: absolute; left: 700px; top: 160px; width: 400px; text-align: center;
    font-family: "Cinzel", Georgia, serif; font-weight: 400; font-size: 64px;
    letter-spacing: 0.5px; color: var(--title-yellow); line-height: 1;
  }
  .title-rule { position: absolute; left: 780px; top: 222px; width: 250px; height: 182px; overflow: visible; }
  .title-honey {
    position: absolute; left: 860px; top: 225px; width: 80px; text-align: center;
    font-family: "Lato", Arial, sans-serif; font-size: 17px; letter-spacing: 1px;
    color: var(--title-yellow); background: var(--paper);
  }
  .photo-jar {
    position: absolute; left: 635px; top: 333px; width: 525px; height: 482px;
    background:
      radial-gradient(ellipse 26% 30% at 62% 52%, #f0b53a 0%, #f2c764 55%, transparent 100%),
      radial-gradient(ellipse 20% 14% at 40% 78%, #f3dc95 0%, #f1e2b0 60%, transparent 100%),
      radial-gradient(ellipse 14% 10% at 24% 50%, #f1c766 0%, transparent 100%),
      radial-gradient(ellipse 12% 16% at 10% 62%, #6e8f3d 0%, transparent 100%),
      linear-gradient(180deg, #ffffff 0%, #f8f6f2 100%);
  }
</style>
</head>
<body>
<main class="flyer">
  <section class="panel-left">
    <div class="mission-box">
      <p>Honey is one of the most ancient nature foods around the world. For thousands of years, as it was enjoyed by our ancients, it has been proved as the healthiest food. Yet, not every person around the world has the opportunity to taste the premium honey or understand what positive effects will the premium honey will bring to their health.</p>
      <p>At Amber Meadow we deeply feel it is our mission to not only provide the most premium Australia Honey to people around the world, but also share our honey knowledge and culture together with everyone.</p>
      <p>It is our mission to introduce the benefit, health effect, culture and receipts of honey products to everyone around the world. To let more people know about honey, enjoy the honey taste and enjoy the benefit that is brought to them through honey.</p>
    </div>
    <div class="brand-mark"><span class="dot"></span><span class="name">Amber Meadow</span></div>
    <div class="photo-blossom" role="img" aria-label="Photo of white blossoms, green leaves and a wooden spoon of honey"></div>
    <p class="address">address should be placed here address should be placed here address should be placed here address should be placed here address should be placed here</p>
  </section>

  <section class="panel-right">
    <div class="brand-small"><span class="dot"></span><span class="name">Amber Meadow</span></div>
    <div class="title-pure">PURE</div>
    <h1 class="title-main">AUSTRALIA</h1>
    <svg class="title-rule" viewBox="0 0 250 182" aria-hidden="true">
      <line x1="10" y1="12" x2="235" y2="12" stroke="#f2e23a" stroke-width="1.5"/>
      <line x1="235" y1="12" x2="235" y2="176" stroke="#f2e23a" stroke-width="1.5"/>
      <circle cx="235" cy="177" r="3.5" fill="#f2e23a"/>
    </svg>
    <div class="title-honey">HONEY</div>
    <div class="photo-jar" role="img" aria-label="Photo of a glass jar of honey with a wooden dipper, honeycomb, a small bowl of honey and an orange flower"></div>
  </section>
</main>
</body>
</html>
```